Business card design for Tervalo Engineering Tandem

We need a new business card design along with all the necessary to place an order. The company is Tervalo Engineering Tandem and we recently updated our logo.

```html
<!DOCTYPE html>
<html lang="en">
<head>
<meta charset="utf-8">
<title>Tervalo Engineering Tandem – Business Card</title>
<link href="https://fonts.googleapis.com/css2?family=Poppins:wght@400;500;600&display=swap" rel="stylesheet">
<style>
  :root {
    --ink: #1d1d1b;
    --black: #000000;
    --paper: #ffffff;
    --canvas: #ffffff;
    --yellow: #e5c600;
    --stone: #9b9a96;
  }
  * { box-sizing: border-box; margin: 0; padding: 0; }
  html, body { width: 1200px; height: 1200px; overflow: hidden; background: var(--canvas); }
  body { position: relative; font-family: "Poppins", sans-serif; color: var(--ink); }

  .card { position: absolute; left: 181px; width: 845px; height: 483px; overflow: hidden; }
  .card--front { top: 94px; background: var(--black); }
  .card--back { top: 630px; background: var(--paper); }

  .wordmark { position: absolute; display: flex; align-items: center; gap: 16px; color: var(--stone); font-weight: 600; }
  .wordmark__square { width: 22px; height: 22px; background: var(--yellow); flex: none; }
  .wordmark__name { display: flex; flex-direction: column; line-height: 1; text-transform: uppercase; }
  .wordmark__primary { letter-spacing: 0.05em; }
  .wordmark__secondary { letter-spacing: 0.12em; margin-top: 8px; }

  .card--front .wordmark { left: 50%; top: 192px; transform: translateX(-50%); }
  .card--front .wordmark__primary { font-size: 70px; }
  .card--front .wordmark__secondary { font-size: 20px; }

  .front-web { position: absolute; right: 51px; top: 422px; font-size: 18px; color: var(--yellow); letter-spacing: 0.02em; }

  .card--back .wordmark { right: 75px; top: 76px; gap: 12px; }
  .card--back .wordmark__square { width: 18px; height: 18px; }
  .card--back .wordmark__primary { font-size: 44px; }
  .card--back .wordmark__secondary { font-size: 13px; margin-top: 6px; }

  .accent-bar { position: absolute; left: 0; top: 204px; width: 15px; height: 74px; background: var(--yellow); }

  .person { position: absolute; left: 75px; top: 205px; }
  .person__name { font-size: 37px; font-weight: 600; letter-spacing: 0.14em; line-height: 1.1; }
  .person__title { font-size: 22px; font-weight: 600; letter-spacing: 0.02em; line-height: 1.2; }

  .divider { position: absolute; left: 75px; top: 293px; width: 695px; height: 2px; background: var(--black); }

  .contacts { position: absolute; left: 75px; top: 318px; list-style: none; }
  .contacts__item { display: flex; align-items: center; height: 25px; margin-bottom: 8.5px; font-size: 17px; letter-spacing: 0.03em; }
  .contacts__item--phone { letter-spacing: 0.16em; }
  .contacts__icon { width: 25px; height: 25px; flex: none; margin-right: 16px; }

  .address { position: absolute; right: 75px; top: 384px; font-size: 17px; }

  .footer-bands { position: absolute; left: 0; bottom: 0; width: 845px; height: 40px; }
</style>
</head>
<body>

  <section class="card card--front">
    <div class="wordmark">
      <span class="wordmark__square"></span>
      <span class="wordmark__name">
        <span class="wordmark__primary">Tervalo</span>
        <span class="wordmark__secondary">Engineering Tandem</span>
      </span>
    </div>
    <p class="front-web">www.yourwebsite.com</p>
  </section>

  <section class="card card--back">
    <div class="wordmark">
      <span class="wordmark__square"></span>
      <span class="wordmark__name">
        <span class="wordmark__primary">Tervalo</span>
        <span class="wordmark__secondary">Engineering Tandem</span>
      </span>
    </div>

    <span class="accent-bar"></span>

    <div class="person">
      <h1 class="person__name">Your Name</h1>
      <p class="person__title">Your Title</p>
    </div>

    <span class="divider"></span>

    <ul class="contacts">
      <li class="contacts__item contacts__item--phone">
        <svg class="contacts__icon" viewBox="0 0 25 25" aria-hidden="true">
          <circle cx="12.5" cy="12.5" r="12.5" fill="#e5c600"/>
          <path d="M8 7.5l2-1 2 3-1.3 1.2c.7 1.6 1.8 2.7 3.4 3.4l1.2-1.3 3 2-1 2c-4.5.5-9.6-4.6-9.3-9.3z" fill="#fff"/>
        </svg>
        123-456-789
      </li>
      <li class="contacts__item">
        <svg class="contacts__icon" viewBox="0 0 25 25" aria-hidden="true">
          <circle cx="12.5" cy="12.5" r="12.5" fill="#e5c600"/>
          <g fill="none" stroke="#fff" stroke-width="1.2">
            <circle cx="12.5" cy="12.5" r="6.5"/>
            <ellipse cx="12.5" cy="12.5" rx="3" ry="6.5"/>
            <path d="M6 12.5h13M7 9h11M7 16h11"/>
          </g>
        </svg>
        www.yourwebsite.com
      </li>
      <li class="contacts__item">
        <svg class="contacts__icon" viewBox="0 0 25 25" aria-hidden="true">
          <circle cx="12.5" cy="12.5" r="12.5" fill="#e5c600"/>
          <g fill="none" stroke="#fff" stroke-width="1.2">
            <rect x="6.5" y="8.5" width="12" height="8"/>
            <path d="M6.5 8.5l6 5 6-5M6.5 16.5l4.5-4M18.5 16.5l-4.5-4"/>
          </g>
        </svg>
        email@info.com
      </li>
    </ul>

    <p class="address">Your Address and Country</p>

    <svg class="footer-bands" viewBox="0 0 845 40" preserveAspectRatio="none" aria-hidden="true">
      <polygon points="0,27 500,27 484,40 0,40" fill="#e5c600"/>
      <polygon points="546,0 845,0 845,40 497,40" fill="#9b9a96"/>
    </svg>
  </section>

</body>
</html>
```